Orthobiologic, StemCell, Bone Marrow Aspirate Device Distributor

We need a wordpress fully functioning website design for an innovative ortho-biologic, Bone Marrow Aspirate Device that extracts stem cells for orthopedic regenerative medical professionals. We also offer state of the art training in there office setting with licensed medical staff, a full service support team, and software for tracking patient outcome over time. We are an innovative company that prides itself on gold standard support. We will have other offerings on our website and would like a spot for "future" products. We would like to see designs that look professional, medical, and convey support, security, science, and innovation. We prefer shades of blue and red/orange. I particularly like the following websites that also sell the same device in order of preference:regenacelltherapy.comhttps://aspire-medical.eu/marrow-cellution/https://www.matrixbiosurgical.com/#emerging-solutions-in-healthcareElite2elite.comI have attached a few pictures of the device for reference

Target Market(s)

Orthopedics, Regenerative medicine doctors, Industry representatives, Hospitals

Industry/Entity Type

Medical Equipment

Coding

Coded - Design and coding required

Colors
3176b5
33a6d7
f37022
ec1f27

Requirements
Must have
• It must be able to have videos which I can supply, email, online ordering, and sfax. I have a domain name Coralweavesolutions.com . It must have a FAQ section which you can obtain some information from https://www.tolvenclinical.com/solutions#resources
• The device is manufactured by Dulmor and this is the link to the product page http://www.dulmor.com/quintadraw
• I am currently working on a custom logo and should be able to supply that in short order. I prefer shades of blue and red.
Nice to have
• I would love to have a graphic video as seen here: please see quinta draw vs bone marrow aspirate concentrate.
• https://www.tolvenclinical.com/solutions#competition
• I would pay considerably more to have something similar if it is at all possible
Should not have
• Nothing specific

```html
<!DOCTYPE html>
<html lang="en">
<head>
<meta charset="utf-8">
<title>Coral Weave Solutions</title>
<link href="https://fonts.googleapis.com/css2?family=Raleway:wght@300;400;500;600;700&family=Lato:wght@400;700&display=swap" rel="stylesheet">
<style>
:root{
  --blue:#3176b5;
  --sky:#33a6d7;
  --orange:#f37022;
  --ink:#222;
  --text:#555;
  --muted:#777;
  --pale:#f1f6fb;
  --footer:#252525;
  --white:#fff;
}
*{box-sizing:border-box;margin:0;padding:0}
html,body{width:1200px;height:3570px;overflow:hidden}
body{font-family:'Lato',sans-serif;color:var(--text);background:var(--white);position:relative}
section,header,footer{position:absolute;left:0;width:1200px}
.abs{position:absolute}
.h{font-family:'Raleway',sans-serif}
.btn{position:absolute;display:flex;align-items:center;justify-content:center;gap:10px;height:54px;border-radius:27px;background:var(--orange);color:var(--white);font-family:'Raleway',sans-serif;font-weight:600;font-size:20px;text-transform:uppercase}
.btn svg{width:19px;height:19px}
.btn.sky{background:var(--sky)}

/* hero */
.hero{top:0;height:654px;background:radial-gradient(circle at 30% 25%,#3f8fc4 0,#1c5d93 30%,#0d3766 70%,#0a2a52 100%)}
.brand{font-family:'Raleway',sans-serif;font-weight:600;color:var(--white);line-height:1.1}
.brand .top{display:block;font-size:40px}
.brand .bottom{display:block;font-size:40px;letter-spacing:3px}
.contact-row{top:30px;right:90px;display:flex;gap:50px;font-size:15px;color:var(--white)}
.contact-row span{display:flex;align-items:center;gap:10px}
.nav{top:80px;right:90px;display:flex;gap:34px;font-family:'Raleway',sans-serif;font-size:18px;font-weight:500;color:var(--white)}
.hero-title{top:272px;width:1200px;text-align:center;font-family:'Raleway',sans-serif;font-weight:700;font-size:44px;color:var(--white)}
.hero-sub{top:342px;width:1200px;text-align:center;font-family:'Raleway',sans-serif;font-weight:500;font-size:31px;line-height:49px;color:var(--white)}

/* welcome */
.welcome{top:654px;height:738px}
.eyebrow{top:112px;width:1200px;text-align:center;font-family:'Raleway',sans-serif;font-weight:300;font-size:26px;color:var(--ink)}
.section-title{width:1200px;text-align:center;font-family:'Raleway',sans-serif;font-weight:700;font-size:36px;color:var(--blue)}
.feature{width:285px}
.feature h3{font-family:'Raleway',sans-serif;font-weight:700;font-size:20px;color:var(--blue);margin-bottom:10px}
.feature h3.dark{color:var(--ink)}
.feature p{font-size:12.5px;line-height:26px;color:var(--text)}
.feature a{display:block;margin-top:6px;font-family:'Raleway',sans-serif;font-weight:600;font-size:16px;color:var(--orange);text-decoration:none}
.rule{height:1px;background:#bbb}
.hub{left:427px;top:246px;width:346px;height:346px;border-radius:50%;background:var(--orange)}
.hub-core{position:absolute;left:32px;top:32px;width:282px;height:282px;border-radius:50%;background:radial-gradient(circle at 40% 30%,#4a8bd0,#1c5aa8 70%);display:flex;align-items:center;justify-content:center;text-align:center;font-family:'Raleway',sans-serif;font-weight:700;font-size:32px;line-height:40px;color:var(--white)}

/* therapies */
.therapies{top:1392px;height:490px}
.panel{position:absolute;top:0;height:490px;color:var(--white)}
.panel.factor{left:0;width:566px;background:radial-gradient(circle at 60% 20%,#3c6fd8 0,#1a3ea8 40%,#0f2a7a 100%)}
.panel.cell{left:568px;width:632px;background:radial-gradient(circle at 70% 40%,#ff8a3a 0,#f2561e 45%,#e63f14 100%)}
.panel h2{position:absolute;top:164px;font-family:'Raleway',sans-serif;font-weight:600;font-size:27px}
.panel p{position:absolute;top:214px;font-family:'Raleway',sans-serif;font-weight:500;font-size:16px;line-height:32px}

/* how it works */
.how{top:1882px;height:582px;background:var(--pale)}
.how h2{position:absolute;left:89px;top:134px;font-family:'Raleway',sans-serif;font-weight:700;font-size:36px;color:var(--blue)}
.how p{position:absolute;left:89px;top:192px;width:480px;font-family:'Raleway',sans-serif;font-size:14.5px;line-height:29.6px;color:var(--muted)}
.video{left:620px;top:121px;width:490px;height:344px;background:linear-gradient(135deg,#eef5f8,#bcdce8 50%,#e8f1f4)}
.play{position:absolute;left:210px;top:137px;width:70px;height:70px}

/* news */
.news{top:2464px;height:682px}
.card{position:absolute;top:197px;width:329px}
.thumb{position:relative;height:194px}
.date{position:absolute;left:14px;bottom:-14px;height:34px;padding:0 14px;display:flex;align-items:center;gap:7px;background:var(--orange);color:var(--white);font-size:14px}
.card h3{margin-top:40px;font-family:'Raleway',sans-serif;font-weight:700;font-size:18px;color:var(--blue)}
.card p{margin-top:10px;font-size:11.5px;line-height:23.5px;text-align:justify;color:var(--text)}
.card a{display:block;margin-top:10px;font-family:'Raleway',sans-serif;font-weight:700;font-size:16px;color:var(--orange);text-decoration:none}

/* footer */
.site-footer{top:3146px;height:424px;background:var(--footer);color:#ddd}
.site-footer h4{position:absolute;top:66px;font-family:'Raleway',sans-serif;font-weight:500;font-size:22px;color:var(--white)}
.fcol{position:absolute;top:122px;font-size:12px;line-height:24px}
.links{list-style:none}
.crow{display:flex;gap:22px;align-items:flex-start;margin-bottom:18px}
.crow svg{flex:none;width:26px;height:26px;margin-top:2px}
.social{display:flex;gap:31px;margin-top:20px;padding-left:14px}
.social span{width:26px;height:26px;border-radius:50%;background:var(--white)}
.divider{top:335px;left:89px;width:1046px;height:1px;background:#555}
.copy{top:372px;width:1200px;text-align:center;font-size:14px;color:#ddd}
</style>
</head>
<body>

<header class="hero" role="img" aria-label="Microscope view of blue stem cells">
  <div class="abs brand" style="left:89px;top:22px"><span class="top">Coral Weave</span><span class="bottom">Solutions</span></div>
  <div class="abs contact-row">
    <span><svg width="18" height="18" viewBox="0 0 24 24" fill="none" stroke="#fff" stroke-width="1.6"><path d="M5 3h4l2 5-2.5 1.5a11 11 0 0 0 6 6L16 13l5 2v4a2 2 0 0 1-2 2A17 17 0 0 1 3 5a2 2 0 0 1 2-2z"/></svg>Call Us: 888-888-8888</span>
    <span><svg width="24" height="18" viewBox="0 0 24 18" fill="none" stroke="#fff" stroke-width="1.5"><rect x="1" y="1" width="22" height="16"/><path d="M1 1l11 9 11-9"/></svg>Email: info@coralweavesolutions.com</span>
  </div>
  <nav class="abs nav"><span>About</span><span>Products</span><span>Providers</span><span>Resources</span><span>Distributors</span><span>FAQ</span><span>Contact</span></nav>
  <h1 class="abs hero-title">AUTOLOGOUS STEM CELLTHERAPY</h1>
  <p class="abs hero-sub">Implementing bone marrow derived stem cells<br>in your practice</p>
  <div class="btn" style="left:497px;top:459px;width:206px">Read More <svg viewBox="0 0 20 20"><circle cx="10" cy="10" r="10" fill="#fff"/><path d="M6 10h7M10 6l4 4-4 4" stroke="#f37022" stroke-width="2.4" fill="none"/></svg></div>
</header>

<section class="welcome">
  <p class="abs eyebrow">WELCOME TO</p>
  <h2 class="abs section-title" style="top:148px">CORAL WEAVE SOLUTIONS</h2>

  <div class="abs rule" style="left:307px;top:290px;width:150px"></div>
  <div class="abs rule" style="left:740px;top:290px;width:90px"></div>
  <div class="abs rule" style="left:307px;top:495px;width:130px"></div>
  <div class="abs rule" style="left:760px;top:495px;width:62px"></div>

  <div class="abs hub"><div class="hub-core" role="img" aria-label="Laboratory test tube in blue light">CORAL WEAVE<br>SOLUTIONS</div></div>

  <div class="abs feature" style="left:89px;top:278px"><h3>ABOUT US</h3><p>Lorem ipsum dolor sit amet, consectetur adip iscing elit, sed do eiusmod tempor incididunt ut labore et dolore magna aliquat.</p><a>Read More</a></div>
  <div class="abs feature" style="left:839px;top:278px"><h3>PROVIDERS</h3><p>Lorem ipsum dolor sit amet, consectetur adip iscing elit, sed do eiusmod tempor incididunt ut labore et dolore magna aliquat.</p><a>Read More</a></div>
  <div class="abs feature" style="left:89px;top:484px"><h3 class="dark">PRODUCTS</h3><p>Lorem ipsum dolor sit amet, consectetur adip iscing elit, sed do eiusmod tempor incididunt ut labore et dolore magna aliquat.</p><a>Read More</a></div>
  <div class="abs feature" style="left:839px;top:484px"><h3>DISTRIBUTORS</h3><p>Lorem ipsum dolor sit amet, consectetur adip iscing elit, sed do eiusmod tempor incididunt ut labore et dolore magna aliquat.</p><a>Read More</a></div>
</section>

<section class="therapies">
  <div class="panel factor" role="img" aria-label="Blue cell cluster background">
    <h2 style="left:89px">FACTOR BASEDTHERAPIES</h2>
    <p style="left:89px">Sud exercitation ullamco lorsi ut aliquip exea<br>ommodo cousaute irure dolor.</p>
    <div class="btn" style="left:89px;top:298px;width:206px">Read More <svg viewBox="0 0 20 20"><circle cx="10" cy="10" r="10" fill="#fff"/><path d="M6 10h7M10 6l4 4-4 4" stroke="#f37022" stroke-width="2.4" fill="none"/></svg></div>
  </div>
  <div class="panel cell" role="img" aria-label="Orange cell cluster background">
    <h2 style="right:90px">CELL BASEDTHERAPIES</h2>
    <p style="right:90px;text-align:right">Sud exercitation ullamco lorsi ut aliquip exea<br>ommodo cousaute irure dolor.</p>
    <div class="btn sky" style="right:90px;top:298px;width:206px">Read More <svg viewBox="0 0 20 20"><circle cx="10" cy="10" r="10" fill="#fff"/><path d="M6 10h7M10 6l4 4-4 4" stroke="#33a6d7" stroke-width="2.4" fill="none"/></svg></div>
  </div>
</section>

<section class="how">
  <h2>HOW IT WORKS</h2>
  <p>Nam libero tempore, cum soluta nobis est eligendi optio cumque nihilir mpe dit quo minus id quod maxime placeat facere possimus, omnis vol uptas ass umenda est, omnis dolor repellendus. Temporibus autem qui busdam etaut officiis debitis aut rerum necessitatibus saepe eveniet ut et voluptates repu diandae sint et molestiae non recusand que earure rum hic tenetur a sapiente delectus.</p>
  <div class="btn" style="left:89px;top:385px;width:206px">Read More <svg viewBox="0 0 20 20"><circle cx="10" cy="10" r="10" fill="#fff"/><path d="M6 10h7M10 6l4 4-4 4" stroke="#f37022" stroke-width="2.4" fill="none"/></svg></div>
  <div class="abs video" role="img" aria-label="Video still of a blue DNA helix between open hands">
    <svg class="play" viewBox="0 0 70 70"><circle cx="35" cy="35" r="35" fill="#111"/><path d="M27 21l22 14-22 14z" fill="#fff"/></svg>
  </div>
</section>

<section class="news">
  <h2 class="abs section-title" style="top:110px">LATEST NEWS</h2>

  <article class="card" style="left:76px">
    <div class="thumb" role="img" aria-label="Pipette dropping liquid into a well plate" style="background:linear-gradient(180deg,#1e5fc8 0,#2f7ad8 55%,#c9d3dd 70%,#7f8c99 100%)"><span class="date"><svg width="13" height="13" viewBox="0 0 14 14" fill="#fff"><rect x="1" y="3" width="12" height="10" rx="1"/><rect x="3" y="0" width="2" height="4"/><rect x="9" y="0" width="2" height="4"/></svg>Aug 17 2018</span></div>
    <h3>SED UT PERSPICIATIS UND</h3>
    <p>Sed ut perspiciatis unde omnis iste natus error sit volup-tatem accusantium doloremque laudantium, totam rem aperiam, eaque ipsa quae ab illo</p>
    <a>READ MORE</a>
  </article>
  <article class="card" style="left:435px">
    <div class="thumb" role="img" aria-label="Gloved hand holding a petri dish" style="background:radial-gradient(circle at 55% 50%,#9fd8f0 0,#5ab7e3 45%,#3a98cf 100%)"><span class="date"><svg width="13" height="13" viewBox="0 0 14 14" fill="#fff"><rect x="1" y="3" width="12" height="10" rx="1"/><rect x="3" y="0" width="2" height="4"/><rect x="9" y="0" width="2" height="4"/></svg>Aug 17 2018</span></div>
    <h3>SED UT PERSPICIATIS UND</h3>
    <p>Sed ut perspiciatis unde omnis iste natus error sit volup-tatem accusantium doloremque laudantium, totam rem aperiam, eaque ipsa quae ab illo</p>
    <a>READ MORE</a>
  </article>
  <article class="card" style="left:794px">
    <div class="thumb" role="img" aria-label="Scientist working with a microscope in a lab" style="background:linear-gradient(90deg,#dfe8ee 0,#f4f7f9 50%,#d4dde4 100%)"><span class="date"><svg width="13" height="13" viewBox="0 0 14 14" fill="#fff"><rect x="1" y="3" width="12" height="10" rx="1"/><rect x="3" y="0" width="2" height="4"/><rect x="9" y="0" width="2" height="4"/></svg>Aug 17 2018</span></div>
    <h3>SED UT PERSPICIATIS UND</h3>
    <p>Sed ut perspiciatis unde omnis iste natus error sit volup-tatem accusantium doloremque laudantium, totam rem aperiam, eaque ipsa quae ab illo</p>
    <a>READ MORE</a>
  </article>
</section>

<footer class="site-footer">
  <h4 style="left:89px">About us</h4>
  <p class="fcol" style="left:89px;width:275px;text-align:justify">Sed ut perspiciatis unde omnis iste nat s error sit voluptatem accusantium dolorem que lau-dantium, totam rem aperiam, eaue ipsa quae ab illo inventoreveritatis et quasi architecto beatae vitae</p>

  <h4 style="left:423px">Links</h4>
  <ul class="fcol links" style="left:423px"><li>About</li><li>Products</li><li>Providers</li><li>Resources</li><li>Distributors</li><li>FAQ</li><li>Contact</li></ul>

  <h4 style="left:574px">Contact Us</h4>
  <div class="fcol" style="left:574px;top:120px">
    <div class="crow"><svg viewBox="0 0 24 24" fill="none" stroke="#ddd" stroke-width="1.4"><path d="M12 22s7-7.5 7-13A7 7 0 0 0 5 9c0 5.5 7 13 7 13z"/><circle cx="12" cy="9" r="2.5"/></svg><span>795 Sgibnjc jhgd Avenue,<br>Dummy Adregk, lkkjasjf</span></div>
    <div class="crow"><svg viewBox="0 0 26 20" fill="none" stroke="#ddd" stroke-width="1.4"><rect x="1" y="1" width="24" height="18"/><path d="M1 1l12 10 12-10"/></svg><span>info@coralweavesolutions.com<br>founder@coralweavesolutions.com</span></div>
    <div class="crow"><svg viewBox="0 0 24 24" fill="none" stroke="#ddd" stroke-width="1.4"><path d="M5 3h4l2 5-2.5 1.5a11 11 0 0 0 6 6L16 13l5 2v4a2 2 0 0 1-2 2A17 17 0 0 1 3 5a2 2 0 0 1 2-2z"/></svg><span>1 888 888 8888<br>1 888 888 9999</span></div>
  </div>

  <div class="abs" style="left:866px;top:112px">
    <div class="brand"><span class="top">Coral Weave</span><span class="bottom">Solutions</span></div>
    <div class="social"><span></span><span></span><span></span><span></span></div>
  </div>

  <div class="abs divider"></div>
  <p class="abs copy">© 2019 All Rights Are Reserved.Terms of Use | Privacy Policy</p>
</footer>

</body>
</html>
```